Werbebrief
Zielgruppe
Unsere Zielgruppe sind Geschäftsführer junger Unternehmen.
Hallo,
Wir benötigen einen "Werbebrief". Es ist jedoch weniger ein Brief, als viel mehr eine etwas größerer "Werbekarte" (diese soll 105 x 210mm groß sein).
Auf der Vorderseite soll folgender Text stehen:
Für Unternehmen, die gerne expandieren möchten
Auf der Rückseite soll folgender Link stehen:
www.feldrok-studio.de/Expandieren
Darunter soll folgendes stehen:
Ihr persönlicher Code: ABC123
Wichtig ist, dass wir den Code individuell ändern können, da jeder einen anderen Code bekommt.
Unser Logo und Corporate Farbe habe ich hochgeladen. Das Design sollte auf jeden Fall zu unserer Webseite passen (www.feldrok-studio.de)
Wir freuen uns auf Ihre Vorschläge.

```html
<!DOCTYPE html>
<html lang="de">
<head>
<meta charset="utf-8">
<title>Feldrok Studio – Werbekarte</title>
<link rel="stylesheet" href="https://fonts.googleapis.com/css2?family=Open+Sans:wght@400&display=swap">
<style>
  :root {
    --page-bg: #e8e5e1;
    --card-top: #24549d;
    --card-bottom: #1b4184;
    --card-text: #ffffff;
    --card-text-soft: #eef2f8;
  }
  * { margin: 0; padding: 0; box-sizing: border-box; }
  html, body {
    width: 1200px;
    height: 1200px;
    overflow: hidden;
    background: var(--page-bg);
    font-family: "Open Sans", Arial, sans-serif;
  }
  .canvas {
    position: relative;
    width: 1200px;
    height: 1200px;
  }
  .card {
    position: absolute;
    left: 170px;
    width: 874px;
    height: 436px;
    background: linear-gradient(180deg, var(--card-top) 0%, var(--card-bottom) 100%);
    box-shadow: 0 6px 18px rgba(0, 0, 0, 0.25);
    color: var(--card-text);
  }
  .card--front { top: 126px; }
  .card--back { top: 650px; }

  .brand {
    position: absolute;
    top: 26px;
    right: 34px;
    display: flex;
    align-items: center;
    gap: 14px;
  }
  .brand__mark {
    width: 22px;
    height: 22px;
    background: var(--card-text);
  }
  .brand__name {
    font-size: 35px;
    font-weight: 400;
    color: var(--card-text);
    line-height: 1;
    letter-spacing: 0.2px;
  }

  .front-claim {
    position: absolute;
    top: 152px;
    left: 136px;
    font-size: 32px;
    line-height: 54px;
    color: var(--card-text-soft);
  }
  .front-claim__line { display: block; white-space: nowrap; }
  .front-claim__line--indent { padding-left: 189px; }

  .back-info {
    position: absolute;
    top: 160px;
    left: 49px;
    font-size: 32px;
    line-height: 56px;
    color: var(--card-text-soft);
  }
  .back-info__url { display: block; white-space: nowrap; }
  .back-info__code {
    display: flex;
    align-items: baseline;
    padding-left: 186px;
    white-space: nowrap;
  }
  .back-info__code-field {
    display: inline-block;
    width: 200px;
    margin-left: 6px;
    border-bottom: 2px solid var(--card-text-soft);
    height: 30px;
  }
</style>
</head>
<body>
<main class="canvas">
  <section class="card card--front" aria-label="Vorderseite">
    <div class="brand">
      <span class="brand__mark"></span>
      <span class="brand__name">Feldrok Studio</span>
    </div>
    <p class="front-claim">
      <span class="front-claim__line">Für Unternehmen, die gerne</span>
      <span class="front-claim__line front-claim__line--indent">expandieren möchten</span>
    </p>
  </section>

  <section class="card card--back" aria-label="Rückseite">
    <div class="brand">
      <span class="brand__mark"></span>
      <span class="brand__name">Feldrok Studio</span>
    </div>
    <div class="back-info">
      <span class="back-info__url">www.feldrok-studio.de/Expandieren</span>
      <span class="back-info__code">Ihr persönlicher Code:<span class="back-info__code-field"></span></span>
    </div>
  </section>
</main>
</body>
</html>
```